The most modern business card ever !!!

Our company call “Vendalo”. Vendalo is a technology company specialized in cruises solutions. Out main product is a platform to reserve cruises. This is a revolutionary platform that make easier to travel agencies and final users to reserve cruises across dozen companies like tibba, wernu, hpv, dgb, etc..We are a “start up”, with a young team of developers and we want to transmit it.. For it, we want something different, a modern business card that represent cruises and technology.. When someone receive this card, this person should say: wowww this is different… this is modern… this is a cruise related company..
- diferent, modern
- traditions business card

```html
<!DOCTYPE html>
<html lang="en">
<head>
<meta charset="utf-8">
<title>Vendalo Business Card</title>
<link rel="stylesheet" href="https://fonts.googleapis.com/css2?family=Ruda:wght@400;700&display=swap">
<style>
  :root {
    --backdrop: #7b7b7b;
    --card-paper: #ececec;
    --ink: #111111;
    --sky: #29a8e0;
    --night: #000000;
    --white: #ffffff;
    --rule: #9a9a9a;
  }
  * { margin: 0; padding: 0; box-sizing: border-box; }
  html, body { width: 1200px; height: 1200px; overflow: hidden; }
  body {
    background: var(--backdrop);
    font-family: "Ruda", sans-serif;
    position: relative;
  }
  .card {
    position: absolute;
    top: 310px;
    width: 364px;
    height: 594px;
    box-shadow: 2px 3px 4px rgba(0,0,0,0.45);
    overflow: hidden;
  }
  .card--front {
    left: 234px;
    background: var(--card-paper);
    color: var(--ink);
    text-align: center;
  }
  .card--back {
    left: 627px;
    width: 369px;
    background: var(--sky);
  }
  .wordmark {
    position: absolute;
    left: 0; right: 0;
    top: 136px;
    font-size: 58px;
    font-weight: 700;
    letter-spacing: 1px;
    color: var(--ink);
  }
  .contact {
    position: absolute;
    left: 0; right: 0;
    top: 342px;
  }
  .contact__name {
    font-size: 24px;
    font-weight: 700;
    color: var(--sky);
    line-height: 28px;
  }
  .contact__role {
    font-size: 18px;
    line-height: 22px;
  }
  .contact__rule {
    width: 208px;
    height: 1px;
    margin: 8px auto 9px;
    background: var(--rule);
  }
  .contact__line {
    font-size: 18px;
    line-height: 24.5px;
  }
  .contact__label { color: var(--sky); font-weight: 700; }
  .contact__web { color: var(--sky); font-weight: 700; }
  .contact__address { font-size: 18px; line-height: 24.5px; }

  .back__band {
    position: absolute;
    left: 0; top: 0;
    width: 100%;
    height: 100px;
    background: var(--night);
  }
  .back__wordmark {
    position: absolute;
    left: 0; right: 0;
    top: 250px;
    text-align: center;
    font-size: 58px;
    font-weight: 700;
    letter-spacing: 1px;
    color: var(--white);
  }
  .back__web {
    position: absolute;
    left: 0; right: 0;
    top: 526px;
    text-align: center;
    font-size: 20px;
    color: var(--white);
  }
</style>
</head>
<body>
  <section class="card card--front">
    <div class="wordmark">Vendalo</div>
    <div class="contact">
      <div class="contact__name">MAREK HALVORSEN</div>
      <div class="contact__role">Managing Director</div>
      <div class="contact__rule"></div>
      <div class="contact__line"><span class="contact__label">P:</span> 044-987 654 321</div>
      <div class="contact__line"><span class="contact__label">M:</span> 044-987 654 321</div>
      <div class="contact__line"><span class="contact__label">E:</span> hello@vendalomail.com</div>
      <div class="contact__line contact__web">www.vendalosail.com</div>
      <div class="contact__rule"></div>
      <div class="contact__address">12345, Address Goes Here</div>
      <div class="contact__address">Country Name, 123456.</div>
    </div>
  </section>

  <section class="card card--back">
    <div class="back__band"></div>
    <div class="back__wordmark">Vendalo</div>
    <div class="back__web">www.vendalosail.com</div>
  </section>
</body>
</html>
```